Wordpress Theme for Cedarway Clinic

** Please view updated Sitemap2.pdf doc to clarify some confusion ***

This is a multiuser WordPress subscription site for Cedarway Clinic. Please see attachment for sitemap. Please do not include extra content like social media icons, search bars, or images. If you have questions, please ask for clarification.
The site contains the following pages and sub-pages:

1. Home
2. Our Clinic
2a. Our Clinic > Mission
2b. Our Clinic > Services
2c. Our Clinic > Clinic Policies
2d. Our Clinic > Schedules
3. Our Staff
3a. Our Staff > [Staff member page]
4. Resources
4a. Resources > Patient Health (index)
4b. Resources > Patient Health (index) > [post]
4c. Resources > Links
4d. Resources > Forms
5. Alerts
5a. Alerts > [Alert Page]
6. Contact Us

Includes the Following Pages, Subpages, and Content
1. Home
a. About Us
b. Our Staff
c. Bulletins
d. Accepting New Patients (shown as an alert widget)
e. Links
i. Physician Toolbox
ii. Book an Appointment
f. Clinic Policies
i. Show first 3 policies (e.g. Late Arrivals, Missed Appointments, Fees)
ii. Link to Clinic Policies page
g. Primary widget (displayed on all pages)
i. Hours of operation
ii. Contact Info
1. Tel
2. Fax
3. Email
4. Address
5. Get directions (link to Google Maps)
2. Our Clinic
a. Main Page
i. Clinic Name
ii. Overview
iii. Languages Spoken
iv. Secondary Navigation
1. Mission
2. Services
3. Clinic Policies
4. Schedules (see attachment)
b. Our Clinic > Mission
c. Our Clinic > Services
i. For each service include service TITLE and DESCRIPTION
d. Our Clinic > Clinic Policies
i. For each policy include policy TITLE and DESCRIPTION
ii. Include the following policies in mockup
1. Late arrivals
2. Missed appointments
3. Fees for missed appointments
4. Referrals and follow-ups
5. Services not covered by RDA
6. Information for LTF patients
7. Medical Legal Reports
e. Our Clinic > Schedules
3. Our Staff
a. Main Page
i. Display a list of staff members. Include NAME and DESIGNATION
b. Our Staff > [Staff Name]
i. Include NAME, PICTURE, DESIGNATION, and BIO
4. Resources
a. Resources > Patient Health
i. Main Page
1. Posts (ordered by date)
a. Title
b. Summary
2. Side Navigation
a. Post Categories
ii. Patient Health > [post title]
1. Title
2. Post Category
3. Date
4. Author
5. Summary
6. Body
b. Resources > Links
1. Secondary Navigation - Categories
a. Sample Categories:
i. Local Services
ii. RDA and Drug Coverage
iii. Mental Health Resources
2. Category page
a. Include the following links in the 'Local Services' category
i. Hypertension clinics
ii. Home Care services
iii. Vaccine Clinics
c. Resources > Forms
i. Display a table with form TITLE and CATEGORY
ii. Side Navigation
1. Form Categories
a. Use the following sample Categories
i. Referrals
ii. Insurance
iii. Intake
iv. Discharge
v. Waivers
5. Alerts
a. Main page
i. List of all Alert posts
1. Include post TITLE as a link to the post
ii. Side Navigation
1. Alerts Archive
a. shown as Month + Number of posts
iii. Alerts > [Alert page]
1. Include TITLE, DATE, AUTHOR, BODY
6. Contact Us
a. Map
b. Hours of operation
c. Address
d. Phone number
e. Fax number
e. Fax number
f. Map
g. Email

Design notes:
- fixed width
- responsive (need designs for mobile, tablet, and desktop)
- simple, dark font, white background
- use Font Awesome icons where needed
- user adds own logo

Target Market(s)

Cedarway Clinic

Industry/Entity Type

Medical

Number of Pages Required

5+ page

Font styles to use
Serif
Sans Serif

Requirements
Must have
• Please keep designs very simple.
• Examples:
• https://www.quolbin.com/install
• http://www.ventrohax.com/company/about-us
• http://brindlequota.org/
• http://www.trosk.com/
Should not have
• Minimal or no use of shadows and gradients

```html
<!DOCTYPE html>
<html lang="en">
<head>
<meta charset="utf-8">
<title>Cedarway Clinic – Mission</title>
<link rel="stylesheet" href="https://fonts.googleapis.com/css2?family=Raleway:wght@400;500;600;700&family=Lato:wght@400;700&display=swap">
<style>
:root{
  --blue:#0b8be3;
  --ink:#2b2b2b;
  --text:#555;
  --rule:#cfcfcf;
  --band:#f6f6f6;
  --footer:#262626;
  --footer-text:#8a8a8a;
  --footer-head:#a0a0a0;
  --photo-a:#c9d6e4;
  --photo-b:#e6ddd2;
}
*{margin:0;padding:0;box-sizing:border-box}
html,body{width:1200px;height:939px;overflow:hidden;background:#fff}
body{position:relative;font-family:"Lato",sans-serif;color:var(--text)}
a{color:inherit;text-decoration:none}
.abs{position:absolute}

.topbar{left:0;top:0;width:1200px;height:30px;background:var(--blue);color:#fff;font-size:9px}
.topbar .help{left:162px;top:10px}
.topbar .sep{top:7px;width:1px;height:16px;background:rgba(255,255,255,.7)}
.topbar .mail{left:288px;top:10px}
.topbar .book{left:868px;top:10px}
.topbar .tool{left:969px;top:10px}

.brand{font-family:"Raleway",sans-serif;font-weight:600;color:var(--ink);font-size:20px;display:flex;align-items:center;gap:12px;white-space:nowrap}
.brand .dot{width:12px;height:12px;border-radius:50%;background:var(--blue)}
.header-brand{left:162px;top:58px}

.mainnav{font-family:"Raleway",sans-serif;font-size:10.5px;font-weight:500;color:var(--ink)}
.mainnav a{position:absolute;top:66px;white-space:nowrap}
.mainnav .active{top:30px;left:632px;width:60px;height:83px;background:var(--blue);color:#fff;text-align:center;padding-top:36px}

.titleband{left:0;top:113px;width:1200px;height:59px;background:var(--band)}
.page-title{left:162px;top:123px;font-family:"Raleway",sans-serif;font-weight:600;font-size:18px;color:var(--ink)}
.crumbs{left:162px;top:150px;font-size:8.5px;color:var(--ink)}

.subnav-title{left:162px;top:216px;font-family:"Raleway",sans-serif;font-size:14px;color:var(--ink)}
.subnav-rule{left:162px;top:237px;width:202px;height:1px;background:var(--rule)}
.subnav a{position:absolute;left:176px;font-family:"Raleway",sans-serif;font-size:11.5px;color:#555}
.subnav a.current{color:var(--blue);font-weight:600}
.subnav .line{position:absolute;left:162px;width:127px;height:1px;background:var(--rule)}

.content{left:387px;top:214px;width:432px}
.content h2{font-family:"Raleway",sans-serif;font-weight:600;font-size:16px;color:var(--ink);margin-bottom:4px}
.content .lead{font-size:11.8px;line-height:15px;color:#555}
.photo{left:387px;top:301px;width:427px;height:232px;border:1px solid #c8d4df;background:linear-gradient(90deg,var(--photo-a) 0%,#d6dde6 45%,var(--photo-b) 100%)}
.body-copy{left:387px;top:553px;width:420px;font-size:10px;line-height:15px;color:#666}
.body-copy p+p{margin-top:15px}

.widget{left:836px;top:209px;width:203px;height:352px;border:1px solid #d5d5d5;border-radius:2px}
.widget-head{left:836px;top:209px;width:203px;height:33px;background:var(--blue);color:#fff;font-family:"Raleway",sans-serif;font-size:14px;font-weight:500;text-align:center;padding-top:7px}
.widget-intro{left:851px;top:250px;width:175px;font-size:8.5px;line-height:14px;color:#666}
.hours{left:851px;top:289px;width:172px;font-size:8.5px;color:#444}
.hours .row{display:flex;justify-content:space-between;height:18px}
.hours .row.today,.hours .holidays{color:var(--blue)}
.widget-rule{left:851px;top:438px;width:172px;height:2px;background:#ccc}
.contact-title{left:851px;top:456px;font-family:"Raleway",sans-serif;font-size:14px;font-weight:500;color:var(--ink)}
.contact-list{left:851px;top:480px;font-size:8.5px;line-height:15px;color:#444}
.contact-list dt{position:absolute;left:0;width:80px}
.contact-list dd{margin-left:81px;width:100px}

.footer-accent{left:0;top:713px;width:1200px;height:3px;background:var(--blue)}
.footer-bg{left:0;top:716px;width:1200px;height:223px;background:var(--footer)}
.footer-brand{left:162px;top:757px}
.footer-brand.brand{color:#fff}
.footer-about{left:162px;top:801px;width:205px;font-size:7.8px;line-height:13.5px;color:#ddd}
.footer-head{position:absolute;font-family:"Raleway",sans-serif;font-weight:500;font-size:14px;color:var(--footer-head)}
.footer-links{font-size:10px;line-height:18px;color:#6f6f6f;display:flex;flex-direction:column}
.footer-links a.lit{color:#ccc}
.footer-contact{left:838px;top:771px;font-size:10px;line-height:15px;color:var(--footer-text)}
.footer-contact dt{position:absolute;left:0}
.footer-contact dd{margin-left:81px}
.footer-rule{left:0;top:903px;width:1200px;height:1px;background:#444}
.legal{top:913px;font-size:10px;color:#777}
</style>
</head>
<body>

<header>
  <div class="abs topbar">
    <span class="abs help">To help Here : 100 200 3000</span>
    <span class="abs sep" style="left:281px"></span>
    <span class="abs mail">Email : Contact@ Cedarway.ca</span>
    <span class="abs book">Book an Appointment</span>
    <span class="abs sep" style="left:962px"></span>
    <span class="abs tool">Physician Toolbox</span>
  </div>

  <a class="abs brand header-brand" href="#"><span class="dot"></span>Cedarway Clinic</a>

  <nav class="mainnav">
    <a href="#" style="left:571px">Home</a>
    <a href="#" class="active">Our Clinic</a>
    <a href="#" style="left:726px">Newsletter</a>
    <a href="#" style="left:818px">Our Staff</a>
    <a href="#" style="left:901px">Resources</a>
    <a href="#" style="left:987px">Contact Us</a>
  </nav>
</header>

<div class="abs titleband"></div>
<h1 class="abs page-title">Mission</h1>
<div class="abs crumbs">Home / Our Clinic / Mission</div>

<aside class="subnav">
  <div class="abs subnav-title">Our Clinic</div>
  <div class="abs subnav-rule"></div>
  <a href="#" style="top:242px">About</a>
  <span class="line" style="top:260px"></span>
  <a href="#" class="current" style="top:264px">Misssion</a>
  <span class="line" style="top:283px"></span>
  <a href="#" style="top:287px">Services</a>
  <span class="line" style="top:305px"></span>
  <a href="#" style="top:309px">Policies</a>
  <span class="line" style="top:328px"></span>
  <a href="#" style="top:332px">Schedules</a>
</aside>

<main>
  <section class="abs content">
    <h2>Our Mission</h2>
    <p class="lead">Lorem Ipsum is simply dummy text of the printing and typesetting industry. Lorem Ipsum has been the industry's standard dummy text ever since the 1500s, when an unknown.</p>
  </section>
  <div class="abs photo" role="img" aria-label="Photo of a smiling doctor in blue scrubs with a family in the background"></div>
  <div class="abs body-copy">
    <p>Lorem Ipsum is simply dummy text of the printing and typesetting industry. Lorem Ipsum has been the industry's standard dummy text ever since the 1500s, when an unknown printer took a galley of type and scrambled it to make a type specimen book. It has survived not only five centuries, but also the leap into electronic typesetting, remaining essentially unchanged.</p>
    <p>Lorem Ipsum is simply dummy text of the printing and typesetting industry. Lorem Ipsum has been the industry's standard dummy text ever since the 1500s, when an unknown.</p>
  </div>
</main>

<aside>
  <div class="abs widget"></div>
  <div class="abs widget-head">Hours of Opration</div>
  <p class="abs widget-intro">Lorem Ipsum is simply dummy text of the printing and typesetting industry.</p>
  <div class="abs hours">
    <div class="row today"><span>Monday :</span><span>8:00 AM - 6:00 PM</span></div>
    <div class="row"><span>Tuesday :</span><span>8:00 AM - 6:00 PM</span></div>
    <div class="row"><span>Wednesday :</span><span>8:00 AM - 6:00 PM</span></div>
    <div class="row"><span>Thursday :</span><span>8:00 AM - 6:00 PM</span></div>
    <div class="row"><span>Friday :</span><span>8:00 AM - 6:00 PM</span></div>
    <div class="row"><span>Saturday :</span><span>9:00 AM - 4:00 PM</span></div>
    <div class="row"><span>Sunday :</span><span>9:00 AM - 4:00 PM</span></div>
    <a class="holidays" href="#">Holidays</a>
  </div>
  <div class="abs widget-rule"></div>
  <div class="abs contact-title">Contact Info</div>
  <dl class="abs contact-list">
    <dt>Telephone :</dt><dd>600-555-0142</dd>
    <dt>Email:</dt><dd>contact@cedarway.ca</dd>
    <dt>Address:</dt><dd>48 Alder Road<br>Kelsford,B. Canada,<br>K2R 4TM</dd>
  </dl>
</aside>

<footer>
  <div class="abs footer-accent"></div>
  <div class="abs footer-bg"></div>
  <a class="abs brand footer-brand" href="#"><span class="dot"></span>Cedarway Clinic</a>
  <p class="abs footer-about">Lorem Ipsum is simply dummy text of the printing and typesetting industry. Lorem Ipsum has been the industry's standard dummy text ever since</p>

  <h3 class="footer-head" style="left:461px;top:746px">Navigation</h3>
  <h3 class="footer-head" style="left:686px;top:746px">Links</h3>
  <h3 class="footer-head" style="left:836px;top:745px">Contact Us</h3>

  <nav class="abs footer-links" style="left:461px;top:770px">
    <a href="#" class="lit">Home</a><a href="#">Our Clinic</a><a href="#">Newsletter</a><a href="#">Our Staff</a><a href="#">Resources</a>
  </nav>
  <nav class="abs footer-links" style="left:686px;top:770px">
    <a href="#">Help</a><a href="#">Support</a><a href="#">Privacy Policy</a>
  </nav>
  <dl class="abs footer-contact">
    <dt>Telephone :</dt><dd>600-555-0142</dd>
    <dt>Email:</dt><dd>contact@cedarway.ca</dd>
    <dt>Address:</dt><dd>48 Alder Road<br>Kelsford,B. Canada,<br>&nbsp;K2R 4TM</dd>
  </dl>

  <div class="abs footer-rule"></div>
  <span class="abs legal" style="left:162px">© 2015 Cedarway Clinic. All Rights Reservsd</span>
  <span class="abs legal" style="left:463px">About Us</span>
  <span class="abs legal" style="left:526px">Terms of Use</span>
  <span class="abs legal" style="left:605px">Privacy Policy</span>
</footer>

</body>
</html>
```